Poster

I need a poster for my business, www.coastalsupperroutesnerja.example which some information about the most important activities (Sangria Tasting, Iberian Ham, Charcuteries & Sherry Wine Tasting, Sailboat Experiences and Picnic Experiences). A3 Format. Social media included (@coastalsupperroutescsr), contact information included.

```html
<!DOCTYPE html>
<html lang="en">
<head>
<meta charset="utf-8">
<title>Coastal Supper Routes – Poster</title>
<link href="https://fonts.googleapis.com/css2?family=Poppins:wght@400;500;600;700;800&family=Great+Vibes&display=swap" rel="stylesheet">
<style>
  :root{
    --stage:#a3a3a3;
    --purple-deep:#351c4f;
    --purple-mid:#5a3f86;
    --gold:#f2a31b;
    --ring:#f3bb4e;
    --cream:#fffbea;
    --wash:#f7dc74;
    --ink:#1f1f1f;
    --white:#ffffff;
  }
  *{margin:0;padding:0;box-sizing:border-box}
  html,body{width:1200px;height:1200px;overflow:hidden;background:var(--stage)}
  .poster{
    position:absolute;left:218px;top:58px;width:765px;height:1083px;overflow:hidden;
    background:
      radial-gradient(ellipse 160px 420px at 0% 55%, rgba(247,220,116,.75), transparent 70%),
      radial-gradient(ellipse 170px 380px at 100% 40%, rgba(247,220,116,.8), transparent 70%),
      radial-gradient(ellipse 260px 200px at 10% 92%, rgba(247,220,116,.45), transparent 70%),
      var(--cream);
    font-family:'Poppins',sans-serif;color:var(--ink);
  }
  .hero{position:absolute;left:0;top:0;width:765px;height:340px}
  .hero-photo{position:absolute;inset:0;
    background:
      linear-gradient(180deg,var(--purple-deep) 0%,rgba(53,28,79,.82) 22%,rgba(92,66,140,.6) 55%,rgba(70,45,110,.75) 100%),
      linear-gradient(90deg,#2a1a3d 0%,#7c6aa8 45%,#9d8fc0 70%,#6a5a98 100%);}
  .hero-edge{position:absolute;left:0;bottom:0;width:765px;height:26px}
  .enjoy{position:absolute;left:0;right:0;top:30px;text-align:center;font-family:'Great Vibes',cursive;font-size:92px;line-height:1;color:var(--white)}
  .rule{position:absolute;top:83px;height:1px;background:rgba(255,255,255,.8);width:140px}
  .rule.left{left:148px}.rule.right{left:487px}
  .title{position:absolute;left:0;right:0;text-align:center;font-weight:700;color:var(--gold);font-size:70px;line-height:1;letter-spacing:-.5px}
  .title.one{top:112px;padding-left:56px}
  .title.two{top:174px}
  .subtitle{position:absolute;left:0;right:0;top:232px;text-align:center;color:var(--white);font-size:41px;line-height:1.2}
  .subtitle b{font-weight:600}
  .activity{position:absolute;left:71px;width:680px;height:140px}
  .activity .photo{position:absolute;left:0;top:0;width:129px;height:129px;border-radius:50%;border:10px solid var(--ring);box-shadow:inset 0 0 0 2px var(--white)}
  .activity h2{position:absolute;left:150px;font-size:21.5px;font-weight:700;line-height:28px;letter-spacing:.1px;white-space:nowrap}
  .activity p{position:absolute;left:150px;font-size:13.3px;line-height:15.5px;width:472px}
  .footer{position:absolute;top:950px;left:0;width:765px;height:110px}
  .brand{position:absolute;left:40px;top:14px;display:flex;align-items:center;gap:10px}
  .brand .mark{width:16px;height:16px;background:var(--gold)}
  .brand span{font-size:14px;font-weight:600;color:var(--ink);line-height:1.25;width:110px}
  .call{position:absolute;left:207px;top:12px}
  .call .label{font-size:16px;font-weight:700;color:var(--gold);line-height:1.4}
  .call .phone{font-size:17px;line-height:1.4}
  .contacts{position:absolute;left:378px;top:10px;font-size:15.5px;line-height:24px}
  .contacts div{display:flex;align-items:center;gap:8px}
  .contacts svg{width:14px;height:14px;flex:none}
</style>
</head>
<body>
<main class="poster">
  <header class="hero">
    <div class="hero-photo" role="img" aria-label="Evening view of hillside apartments and lights along the coast"></div>
    <svg class="hero-edge" viewBox="0 0 765 26" preserveAspectRatio="none" aria-hidden="true">
      <path d="M0 10 L40 14 L70 8 L110 16 L150 10 L190 17 L230 9 L270 15 L310 11 L350 18 L390 10 L430 16 L470 12 L510 17 L550 10 L590 15 L630 11 L670 18 L710 12 L750 16 L765 10 L765 26 L0 26Z" fill="var(--cream)"/>
    </svg>
    <div class="rule left"></div><div class="rule right"></div>
    <div class="enjoy">Enjoy</div>
    <div class="title one">MARBELLA <span style="font-weight:500">&amp;</span></div>
    <div class="title two">ESTEPONA</div>
    <div class="subtitle">with <b>Coastal Supper Routes</b></div>
  </header>

  <section class="activity" style="top:356px">
    <div class="photo" role="img" aria-label="Couple tasting red sangria at a table" style="background:linear-gradient(135deg,#8a6a5a,#d9cfc8 60%,#6a3b4a)"></div>
    <h2 style="top:1px">SANGRIA TASTING</h2>
    <p style="top:33px">During this experience, you will try four distinct types of authentic Sangria, each crafted with different wines and fresh, locally sourced ingredients.<br><br>As you sip, immerse yourself in the vibrant atmosphere of Estepona, enjoying the flavors of marinated olives and local cheese included with your booking.</p>
  </section>

  <section class="activity" style="top:502px">
    <div class="photo" role="img" aria-label="Bowl of olives and cured ham bites on a board" style="background:linear-gradient(160deg,#7b6a58,#3a2c22 55%,#1f1a16)"></div>
    <h2 style="top:9px">IBERIAN HAM, CHARCUTERIES &amp;<br>SHERRY WINE TASTING</h2>
    <p style="top:70px">Indulge in the rich flavors of Spain with our Iberian Charcuteries &amp; Sherry Wine Tasting. Sample two premium Iberian hams, three distinct sausages, and a variety of olives, all perfectly paired with a selection of Sherry wines.</p>
  </section>

  <section class="activity" style="top:648px">
    <div class="photo" role="img" aria-label="Sailboat on the sea at sunset" style="background:linear-gradient(180deg,#6f7f99,#c9c2b8 50%,#3c5670 62%,#1f3047)"></div>
    <h2 style="top:11px">SAILBOAT EXPERIENCES</h2>
    <p style="top:43px">The Sailboat Sangria Tasting Experience is a unique and enchanting journey where you can relax and unwind while sailing along the beautiful coast of Estepona. Sip on exquisite artisanal sangria and enjoy gourmet appetizers in a serene setting.</p>
  </section>

  <section class="activity" style="top:794px">
    <div class="photo" role="img" aria-label="Picnic basket with pastries and wine by the sea" style="background:linear-gradient(170deg,#7e9bb8,#c9b9a6 45%,#8a4f35 70%,#e0c9a8)"></div>
    <h2 style="top:14px">PICNIC EXPERIENCES</h2>
    <p style="top:46px">Indulge in a unique morning retreat with our Picnic Brunch Experience from Estepona to Playa Serena. Select from our gourmet picnic basket filled with freshly baked pastries, artisanal cheeses, cured meats, seasonal fruits, and decadent desserts.</p>
  </section>

  <footer class="footer">
    <div class="brand"><div class="mark"></div><span>COASTAL SUPPER ROUTES</span></div>
    <div class="call"><div class="label">CALL US NOW</div><div class="phone">0034 600 000 123</div></div>
    <div class="contacts">
      <div><svg viewBox="0 0 14 14" aria-hidden="true"><rect x="1" y="3" width="12" height="8" fill="var(--gold)"/><path d="M1 3 L7 8 L13 3" stroke="var(--white)" stroke-width="1.2" fill="none"/></svg>info@coastalsupperroutesnerja.example</div>
      <div><svg viewBox="0 0 14 14" aria-hidden="true"><g fill="none" stroke="var(--gold)" stroke-width="1.2"><circle cx="7" cy="7" r="6"/><ellipse cx="7" cy="7" rx="2.6" ry="6"/><path d="M1 7h12M2 4h10M2 10h10"/></g></svg>www.coastalsupperroutesnerja.example</div>
      <div><svg viewBox="0 0 14 14" aria-hidden="true"><g fill="none" stroke="var(--gold)" stroke-width="1.2"><circle cx="7" cy="7" r="2.6"/><path d="M9.6 5v3a1.8 1.8 0 0 0 3.4 0V7a6 6 0 1 0-2.4 4.8"/></g></svg>@coastalsupperroutescsr</div>
    </div>
  </footer>
</main>
</body>
</html>
```